Private Investigation Business Card Design

I need a business card for a new private investigation company named Brisk Inquiries. I perform mainly surveillance jobs, vehicle repossessions, document serves etc. The final design should aim for a professional look. The logo has a magnifying glass with stick man arms and legs and is in a running action to show the "Brisk" aspect of the name. If the colour scheme could remain the same as the website www.briskinquiries-demo.com.au with silvers,blacks and a couple electric blue highlights.
Industry/Entity Type
Business
Contact Information for Business Card
Morgan Kellaway
Brisk Inquiries
0487316204
PO Box 58, Carnwell NSW 2291
info@briskinquiries-demo.com.au
www.briskinquiries-demo.com.au
Look and feel

```html
<!DOCTYPE html>
<html lang="en">
<head>
<meta charset="utf-8">
<title>Brisk Inquiries – Business Card</title>
<link href="https://fonts.googleapis.com/css2?family=Arimo:wght@400;700&display=swap" rel="stylesheet">
<style>
  :root {
    --stage: #2b2b2b;
    --paper: #ffffff;
    --silver-light: #e9e8ea;
    --silver-mid: #c9c8cc;
    --silver-dark: #9f9ea3;
    --ink: #2a2a2c;
    --ink-soft: #4a4a4e;
    --rule: #6d6d72;
  }
  * { box-sizing: border-box; margin: 0; padding: 0; }
  html, body { width: 1200px; height: 750px; overflow: hidden; }
  body {
    background: var(--stage);
    font-family: "Arimo", Arial, sans-serif;
    color: var(--ink);
    position: relative;
  }
  .card {
    position: absolute;
    width: 525px;
    height: 300px;
    top: 225px;
    box-shadow: 0 6px 18px rgba(0,0,0,.45);
    overflow: hidden;
  }
  /* Back of card */
  .card-back {
    left: 50px;
    background: radial-gradient(ellipse at 50% 35%, var(--silver-light) 0%, var(--silver-mid) 55%, var(--silver-dark) 100%);
  }
  .back-brand {
    position: absolute;
    top: 88px;
    left: 0; right: 0;
    display: flex;
    align-items: center;
    justify-content: center;
    gap: 12px;
    font-weight: 700;
    font-size: 34px;
    color: var(--ink);
  }
  .brand-dot {
    width: 30px; height: 30px;
    border-radius: 50%;
    background: var(--ink);
  }
  .social-row {
    position: absolute;
    top: 196px;
    left: 0; right: 0;
    display: flex;
    align-items: center;
    justify-content: center;
    gap: 6px;
  }
  .social-rule {
    width: 90px; height: 1px;
    background: var(--rule);
  }
  .social-spot {
    width: 18px; height: 18px;
    border-radius: 50%;
    background: var(--ink);
  }
  /* Front of card */
  .card-front {
    left: 625px;
    background: var(--paper);
  }
  .front-band {
    position: absolute;
    left: 0; top: 0;
  }
  .front-brand {
    position: absolute;
    top: 46px;
    left: 0; right: 0;
    display: flex;
    align-items: center;
    justify-content: center;
    gap: 10px;
    font-weight: 700;
    font-size: 38px;
    color: var(--silver-dark);
  }
  .front-brand .brand-dot {
    width: 26px; height: 26px;
    background: var(--silver-dark);
  }
  .holder {
    position: absolute;
    left: 40px;
    top: 190px;
  }
  .holder-name {
    font-weight: 700;
    font-size: 17px;
    color: var(--ink);
    margin-bottom: 6px;
  }
  .holder-address {
    font-size: 12.5px;
    line-height: 1.45;
    color: var(--ink-soft);
  }
  .contacts {
    position: absolute;
    right: 22px;
    top: 162px;
    list-style: none;
    text-align: right;
    font-size: 11.5px;
    color: var(--ink-soft);
  }
  .contacts li {
    display: flex;
    align-items: center;
    justify-content: flex-end;
    gap: 7px;
    height: 19px;
  }
  .contacts svg { width: 12px; height: 12px; fill: var(--ink); }
</style>
</head>
<body>

  <section class="card card-back" aria-label="Card back">
    <div class="back-brand"><span class="brand-dot"></span><span>Brisk Inquiries</span></div>
    <div class="social-row" aria-label="Social profiles">
      <span class="social-rule"></span>
      <span class="social-spot"></span>
      <span class="social-spot"></span>
      <span class="social-spot"></span>
      <span class="social-spot"></span>
      <span class="social-rule"></span>
    </div>
  </section>

  <section class="card card-front" aria-label="Card front">
    <svg class="front-band" width="525" height="300" viewBox="0 0 525 300" aria-hidden="true">
      <defs>
        <linearGradient id="silverBand" x1="0" y1="0" x2="1" y2="1">
          <stop offset="0" stop-color="#d8d7da"/>
          <stop offset="0.5" stop-color="#ecebed"/>
          <stop offset="1" stop-color="#bdbcc0"/>
        </linearGradient>
      </defs>
      <path d="M0 140 H52 L62 128 L72 140 H525 V300 H0 Z" fill="url(#silverBand)"/>
      <path d="M0 140 H52 L62 128 L72 140 H525" fill="none" stroke="#55555a" stroke-width="2"/>
    </svg>

    <div class="front-brand"><span>Brisk Inquiries</span><span class="brand-dot"></span></div>

    <div class="holder">
      <p class="holder-name">Morgan Kellaway</p>
      <p class="holder-address">PO Box 58<br>Carnwell NSW 2291</p>
    </div>

    <ul class="contacts">
      <li>0487 316 204
        <svg viewBox="0 0 12 12"><path d="M2 1h2.5l1 3-1.5 1a6 6 0 0 0 3 3l1-1.5 3 1V10a1.5 1.5 0 0 1-1.5 1.5A9.5 9.5 0 0 1 .5 2.5 1.5 1.5 0 0 1 2 1z"/></svg>
      </li>
      <li>info@briskinquiries-demo.com.au
        <svg viewBox="0 0 12 12"><path d="M0 2.5h12v7H0z M0.8 3.2 6 7 11.2 3.2" stroke="#fff" stroke-width=".8"/></svg>
      </li>
      <li>www.briskinquiries-demo.com.au
        <svg viewBox="0 0 12 12"><circle cx="6" cy="6" r="5.5"/><path d="M.5 6h11M6 .5c-3 3-3 8 0 11M6 .5c3 3 3 8 0 11" fill="none" stroke="#fff" stroke-width=".7"/></svg>
      </li>
    </ul>
  </section>

</body>
</html>
```